VORNAK SYSTEMS BUSINESS CARD DESIGN

WE WANT COMPLETE NEW DESIGN OF OUR BUSINESS CARD. WE ARE AN INTEGRATION COMPANY, WHERE WE INTEGRATE IOT/SMART SYSTEMS TO HOMES AND CORPORATE CUSTOMERS. WE SUPPLY AND INSTALL AUTOMATION PRODUCTS. THE FINAL DESIGN SHOULD COMMUNICATE TECHNOLOGY. THE CARD DESIGN SHOULD BE VERY IMPACT FULL. LOGO NEEDS TO BE THERE. IT WOULD NICE IF THE DESIGN WAS CLEAN. COLORS IS UP TO DESIGNER TO PLAY WITH, OR CAN STICK TO CORPORATE COLORS (FOLLOW LOGO). I HAVE ADDED FEW REFERENCE PHOTOS TO DRAW INSPIRATION MAYBE. I HAVE ADDED A HEX DESIGN, ITS NOT NECESSARY TO USE THIS DESIGN, ITS UPTO DESIGNER, JUST ADDED IF NEEDED TO PLAY WITH DESIGN.

Target Market(s)

Private end users and corporate clients

Industry/Entity Type

technology, home automation, home theaters, building management systems, IOT

Contact Information for Business Card

It should include Employee name, personal number, office number, email address, both in English and arabic. DETAILS TO INCLUDE :RAJESH PALLIVAL, MOBILE 0097150738265,OFFCIE 009714368547, RAJESH@VORNAKSYS.EXAMPLE

Requirements
Must have
• Should feel like a technology company from design. Details both and in English and arabic (or at least have provision for arabic in design).
Nice to have
• I would like logo on one side, and details on the other side. Logo design side should communicate technology with logo. Other side can be clean just with information or also have some design aspects following from logo side. it would be interesting to see submissions with square design as well (that looks like an app Icon). colors could be of logo, red black grey and white. I have added some designs to draw inspiration from

```html
<!DOCTYPE html>
<html lang="en">
<head>
<meta charset="utf-8">
<title>Vornak Systems Business Card</title>
<link rel="stylesheet" href="https://fonts.googleapis.com/css2?family=Libre+Baskerville:wght@400;700&family=Open+Sans:wght@400;600&display=swap">
<style>
  :root {
    --bg: #e7e5e2;
    --card-white: #ffffff;
    --card-black: #121212;
    --brand-red: #e0303a;
    --ink: #2b2b2b;
    --grey-dark: #4a4a4c;
    --emboss: #3a3a3a;
  }
  * { box-sizing: border-box; margin: 0; padding: 0; }
  html, body { width: 1200px; height: 913px; overflow: hidden; }
  body {
    background: var(--bg);
    position: relative;
    font-family: "Libre Baskerville", Georgia, serif;
  }
  .card {
    position: absolute;
    top: 308px;
    width: 520px;
    height: 297px;
    border-radius: 3px;
    box-shadow: 0 10px 28px rgba(0,0,0,0.22);
    overflow: hidden;
  }
  .card--front { left: 50px; background: var(--card-white); }
  .card--back  { left: 630px; background: linear-gradient(135deg, #1d1d1d 0%, var(--card-black) 60%, #050505 100%); }

  .contact { position: absolute; left: 30px; top: 78px; width: 260px; }
  .contact__name {
    color: var(--brand-red);
    font-weight: 700;
    font-size: 21px;
    letter-spacing: 0.5px;
    white-space: nowrap;
  }
  .contact__title {
    font-family: "Open Sans", Arial, sans-serif;
    color: var(--ink);
    font-size: 14px;
    margin-top: 4px;
  }
  .contact__list { list-style: none; margin-top: 22px; }
  .contact__item {
    display: flex;
    align-items: center;
    gap: 9px;
    color: var(--ink);
    font-size: 12px;
    margin-bottom: 7px;
    white-space: nowrap;
  }
  .contact__icon { width: 13px; height: 13px; flex: none; }

  .front-brand {
    position: absolute;
    left: 300px; top: 0;
    width: 220px; height: 297px;
    display: flex;
    flex-direction: column;
    align-items: center;
    justify-content: center;
    gap: 18px;
  }
  .front-brand__dot { width: 96px; height: 96px; border-radius: 50%; background: var(--brand-red); }
  .front-brand__name {
    color: var(--grey-dark);
    font-weight: 700;
    font-size: 22px;
    letter-spacing: 2px;
    line-height: 1.25;
    text-align: center;
  }

  .back-brand {
    position: absolute;
    inset: 0;
    display: flex;
    align-items: center;
    justify-content: center;
    gap: 14px;
  }
  .back-brand__mark { width: 34px; height: 34px; background: var(--emboss); }
  .back-brand__name {
    color: var(--emboss);
    font-weight: 700;
    font-size: 34px;
    letter-spacing: 2px;
  }
</style>
</head>
<body>
  <section class="card card--front" aria-label="Business card front">
    <div class="contact">
      <p class="contact__name">RAJESH PALLIVAL</p>
      <p class="contact__title">Managing Director</p>
      <ul class="contact__list">
        <li class="contact__item">
          <svg class="contact__icon" viewBox="0 0 16 16" aria-hidden="true"><path fill="#e0303a" d="M2 6c0-2 3-3 6-3s6 1 6 3v1h-3V6H5v1H2zM4 8h8l2 5H2z"/></svg>
          <span>009714368547</span>
        </li>
        <li class="contact__item">
          <svg class="contact__icon" viewBox="0 0 16 16" aria-hidden="true"><rect x="4" y="1" width="8" height="14" rx="1.5" fill="#e0303a"/><rect x="5.5" y="3" width="5" height="8" fill="#fff"/></svg>
          <span>0097150738265</span>
        </li>
        <li class="contact__item">
          <svg class="contact__icon" viewBox="0 0 16 16" aria-hidden="true"><rect x="1" y="3" width="14" height="10" fill="#e0303a"/><path d="M1 3l7 6 7-6" fill="none" stroke="#fff" stroke-width="1.2"/></svg>
          <span>RAJESH@VORNAKSYS.EXAMPLE</span>
        </li>
      </ul>
    </div>
    <div class="front-brand">
      <span class="front-brand__dot"></span>
      <span class="front-brand__name">VORNAK<br>SYSTEMS</span>
    </div>
  </section>

  <section class="card card--back" aria-label="Business card back">
    <div class="back-brand">
      <span class="back-brand__mark"></span>
      <span class="back-brand__name">VORNAK SYSTEMS</span>
    </div>
  </section>
</body>
</html>
```